2021 Summer Ads Hollis Bay Custom Homes

We need a re-design of our summer ad run for our customer, Hollis Bay Custom Homes. They are custom home builders in the mostly rural parts of West Virginia, USA. They are known for their "Forever Home" tagline. We'd like two designed ads with the main difference being just the custom home that's featured. These designs should be for a Zintrola banner like 300 x 250 and square ad like 250 x 250. For inspiration please visit the Hollis Bay Custom Homes website at www dot hollisbaycustomhomes dot com

Target Market(s)

consumers / new home shoppers

Industry/Entity Type

Consumer

Requirements
Must have
• HBCH logo
Price Lock Available!
Custom home pic
Learn more >
small CFRM logo mark

```html
<!DOCTYPE html>
<html lang="en">
<head>
<meta charset="utf-8">
<title>Hollis Bay Custom Homes – Summer Ads 2021</title>
<link rel="stylesheet" href="https://fonts.googleapis.com/css2?family=Montserrat:wght@500;600;700;800&display=swap">
<style>
  :root{
    --board:#ebebeb;
    --ink:#1b1c22;
    --navy:#161a2c;
    --navy-deep:#0e1120;
    --red:#e3192b;
    --red-deep:#a30d1c;
    --red-dark:#6e0a14;
    --white:#ffffff;
    --dusk-top:#c9b6d8;
    --dusk-mid:#e9c7b4;
    --stone:#7a5a48;
    --sky:#e6eef3;
    --siding:#f1f2f0;
    --grass:#4f7a35;
  }
  *{box-sizing:border-box;margin:0;padding:0}
  html,body{width:1200px;height:1091px;overflow:hidden;background:var(--board)}
  body{font-family:"Montserrat",Arial,sans-serif;position:relative}

  .size-label{position:absolute;top:58px;width:390px;text-align:center;
    font-weight:800;font-size:62px;letter-spacing:1px;color:var(--ink);line-height:1}
  .size-label--square{left:118px}
  .size-label--banner{left:652px}

  .ad{position:absolute;overflow:hidden;color:var(--white)}
  .ad--square{width:390px;height:389px;left:123px}
  .ad--banner{width:467px;height:389px;left:633px}
  .ad--top{top:168px}
  .ad--bottom{top:606px}

  .ad__photo{position:absolute;top:0;right:0;height:100%}
  .ad__photo--dusk{width:70%;
    background:linear-gradient(180deg,var(--dusk-top) 0%,#eadbe6 30%,#f4efe9 48%,var(--stone) 75%,#9d8d80 100%)}
  .ad__photo--day{width:66%;
    background:linear-gradient(180deg,var(--sky) 0%,#dfe3e3 22%,var(--siding) 40%,#e3e5e2 70%,var(--grass) 86%,#3f6a2b 100%)}

  .ad__panel{position:absolute;inset:0;width:100%;height:100%}

  .ad__content{position:absolute;inset:0}
  .brand{position:absolute;display:flex;align-items:center;gap:7px;
    font-weight:700;font-size:17px;letter-spacing:1px;color:var(--white);white-space:nowrap}
  .brand__mark{width:12px;height:12px;background:var(--white)}

  .headline{position:absolute;text-transform:uppercase;line-height:1.2}
  .headline__lead{display:block;font-weight:500}
  .headline__strong{display:block;font-weight:700}

  .offer{position:absolute;font-weight:700;text-transform:uppercase;white-space:nowrap}

  .cta{position:absolute;display:flex;align-items:center;justify-content:space-between;
    font-weight:700;text-transform:uppercase;color:var(--white);border-radius:2px;overflow:hidden}
  .cta__label{flex:1;text-align:center;letter-spacing:.3px}
  .cta--red{background:var(--red)}
  .cta--red .cta__arrow{background:var(--red-deep);height:100%;display:flex;align-items:center;justify-content:center}
  .cta--navy{background:var(--navy)}
  .cta--navy .cta__arrow{background:var(--red);border-radius:50%;display:flex;align-items:center;justify-content:center;margin-right:-2px}

  .partner{position:absolute;display:flex;flex-direction:column;color:var(--white)}
  .partner__name{font-weight:800;font-size:25px;letter-spacing:.5px;line-height:1;display:flex;align-items:center;gap:6px}
  .partner__mark{width:9px;height:9px;background:var(--white)}
  .partner__sub{font-weight:500;font-size:8.5px;line-height:1.2;margin-top:3px;width:98px}
</style>
</head>
<body>

  <h2 class="size-label size-label--square">250 X 250</h2>
  <h2 class="size-label size-label--banner">300 X 250</h2>

  <!-- Square, dusk house -->
  <section class="ad ad--square ad--top" aria-label="Square ad, dusk home">
    <div class="ad__photo ad__photo--dusk" role="img" aria-label="Photo of a two-storey custom home with a blue metal roof and lit screened porch at dusk"></div>
    <svg class="ad__panel" viewBox="0 0 250 250" preserveAspectRatio="none" aria-hidden="true">
      <defs>
        <linearGradient id="stripeA" x1="0" y1="0" x2="0" y2="1">
          <stop offset="0" stop-color="#e3192b"/><stop offset="1" stop-color="#8e0b18"/>
        </linearGradient>
      </defs>
      <polygon points="0,0 178,0 112,250 0,250" fill="#161a2c"/>
      <polygon points="178,0 190,0 124,250 112,250" fill="url(#stripeA)"/>
      <polygon points="120,0 178,0 168,36" fill="#b3101f" opacity=".85"/>
      <rect x="0" y="244" width="250" height="6" fill="#e3192b"/>
    </svg>
    <div class="ad__content">
      <div class="brand" style="left:14px;top:38px"><span class="brand__mark"></span>HOLLIS BAY</div>
      <p class="headline" style="left:12px;top:98px;font-size:21px;line-height:28px">
        <span class="headline__lead">Start Building</span>
        <span class="headline__strong">Your Forever</span>
        <span class="headline__strong">Home Today!</span>
      </p>
      <p class="offer" style="left:12px;top:192px;font-size:11px">Price Lock Available!</p>
      <a class="cta cta--red" style="left:12px;top:224px;width:129px;height:34px;font-size:10px">
        <span class="cta__label">Learn More</span>
        <span class="cta__arrow" style="width:26px"><svg width="10" height="14" viewBox="0 0 10 14"><path d="M2 1l6 6-6 6" fill="none" stroke="#fff" stroke-width="2.6"/></svg></span>
      </a>
      <div class="partner" style="left:14px;top:288px">
        <span class="partner__name"><span class="partner__mark"></span>CFRM</span>
        <span class="partner__sub">Council of Family Residence Makers</span>
      </div>
    </div>
  </section>

  <!-- Banner, dusk house -->
  <section class="ad ad--banner ad--top" aria-label="Banner ad, dusk home">
    <div class="ad__photo ad__photo--dusk" style="width:68%" role="img" aria-label="Photo of a two-storey custom home with a blue metal roof and lit screened porch at dusk"></div>
    <svg class="ad__panel" viewBox="0 0 300 250" preserveAspectRatio="none" aria-hidden="true">
      <defs>
        <linearGradient id="stripeB" x1="0" y1="0" x2="0" y2="1">
          <stop offset="0" stop-color="#e3192b"/><stop offset="1" stop-color="#8e0b18"/>
        </linearGradient>
      </defs>
      <polygon points="0,0 190,0 112,250 0,250" fill="#161a2c"/>
      <polygon points="190,0 202,0 124,250 112,250" fill="url(#stripeB)"/>
      <polygon points="135,0 190,0 180,32" fill="#b3101f" opacity=".85"/>
    </svg>
    <div class="ad__content">
      <div class="brand" style="left:18px;top:40px"><span class="brand__mark"></span>HOLLIS BAY</div>
      <p class="headline" style="left:16px;top:96px;font-size:24px;line-height:30px">
        <span class="headline__lead">Start Building</span>
        <span class="headline__strong">Your Forever</span>
        <span class="headline__strong">Home Today!</span>
      </p>
      <p class="offer" style="left:16px;top:196px;font-size:12px">Price Lock Available!</p>
      <a class="cta cta--red" style="left:11px;top:234px;width:151px;height:40px;font-size:11px">
        <span class="cta__label">Learn More</span>
        <span class="cta__arrow" style="width:30px"><svg width="11" height="16" viewBox="0 0 10 14"><path d="M2 1l6 6-6 6" fill="none" stroke="#fff" stroke-width="2.6"/></svg></span>
      </a>
      <div class="partner" style="left:20px;top:300px">
        <span class="partner__name"><span class="partner__mark"></span>CFRM</span>
        <span class="partner__sub">Council of Family Residence Makers</span>
      </div>
    </div>
  </section>

  <!-- Square, white farmhouse -->
  <section class="ad ad--square ad--bottom" aria-label="Square ad, farmhouse">
    <div class="ad__photo ad__photo--day" role="img" aria-label="Photo of a white board-and-batten farmhouse with a metal roof and green lawn"></div>
    <svg class="ad__panel" viewBox="0 0 250 250" preserveAspectRatio="none" aria-hidden="true">
      <defs>
        <linearGradient id="panelC" x1="0" y1="0" x2="1" y2="1">
          <stop offset="0" stop-color="#c8142a"/><stop offset=".6" stop-color="#9a0f1e"/><stop offset="1" stop-color="#6e0a14"/>
        </linearGradient>
      </defs>
      <path d="M0,0 H168 Q232,120 162,250 H0 Z" fill="#e3192b"/>
      <path d="M0,0 H160 Q222,120 154,250 H0 Z" fill="#ffffff"/>
      <path d="M0,0 H152 Q212,122 146,250 H0 Z" fill="url(#panelC)"/>
    </svg>
    <div class="ad__content">
      <div class="brand" style="left:20px;top:72px"><span class="brand__mark"></span>HOLLIS BAY</div>
      <p class="headline" style="left:19px;top:127px;font-size:21px;line-height:29px">
        <span class="headline__lead">Start Building</span>
        <span class="headline__strong">Your Forever</span>
        <span class="headline__strong">Home Today!</span>
      </p>
      <p class="offer" style="left:19px;top:225px;font-size:11px">Price Lock Available!</p>
      <a class="cta cta--navy" style="left:19px;top:260px;width:146px;height:37px;font-size:10.5px">
        <span class="cta__label">Learn More</span>
        <span class="cta__arrow" style="width:34px;height:34px"><svg width="10" height="14" viewBox="0 0 10 14"><path d="M2 1l6 6-6 6" fill="none" stroke="#fff" stroke-width="2.6"/></svg></span>
      </a>
      <div class="partner" style="left:22px;top:316px">
        <span class="partner__name"><span class="partner__mark"></span>CFRM</span>
        <span class="partner__sub">Council of Family Residence Makers</span>
      </div>
    </div>
  </section>

  <!-- Banner, white farmhouse -->
  <section class="ad ad--banner ad--bottom" aria-label="Banner ad, farmhouse">
    <div class="ad__photo ad__photo--day" style="width:72%" role="img" aria-label="Photo of a white board-and-batten farmhouse with a metal roof and green lawn"></div>
    <svg class="ad__panel" viewBox="0 0 300 250" preserveAspectRatio="none" aria-hidden="true">
      <defs>
        <linearGradient id="panelD" x1="0" y1="0" x2="1" y2="1">
          <stop offset="0" stop-color="#c8142a"/><stop offset=".6" stop-color="#9a0f1e"/><stop offset="1" stop-color="#6e0a14"/>
        </linearGradient>
      </defs>
      <path d="M0,0 H172 Q240,125 166,250 H0 Z" fill="#e3192b"/>
      <path d="M0,0 H164 Q230,125 158,250 H0 Z" fill="#ffffff"/>
      <path d="M0,0 H156 Q220,126 150,250 H0 Z" fill="url(#panelD)"/>
    </svg>
    <div class="ad__content">
      <div class="brand" style="left:20px;top:62px"><span class="brand__mark"></span>HOLLIS BAY</div>
      <p class="headline" style="left:19px;top:112px;font-size:22px;line-height:30px">
        <span class="headline__lead">Start Building</span>
        <span class="headline__strong">Your Forever</span>
        <span class="headline__strong">Home Today!</span>
      </p>
      <p class="offer" style="left:21px;top:209px;font-size:11px">Price Lock Available!</p>
      <a class="cta cta--navy" style="left:20px;top:241px;width:126px;height:34px;font-size:10px">
        <span class="cta__label">Learn More</span>
        <span class="cta__arrow" style="width:31px;height:31px"><svg width="10" height="14" viewBox="0 0 10 14"><path d="M2 1l6 6-6 6" fill="none" stroke="#fff" stroke-width="2.6"/></svg></span>
      </a>
      <div class="partner" style="left:22px;top:302px">
        <span class="partner__name"><span class="partner__mark"></span>CFRM</span>
        <span class="partner__sub">Council of Family Residence Makers</span>
      </div>
    </div>
  </section>

</body>
</html>
```